Boutique custom software development company needs new business card

Our nearly 20 year old custom software development company would like to better include the fact that we are now providing Bitcoin services. These new services are B2B include education (how to acquire and securely hold Bitcoin) and integrating Bitcoin payments into existing ecommerce sites or other existing systems. Please keep the card clean and simple. Attached is our current design and some other files. vextorial.com

Target Market(s)

businesses owners interested in long term relationship

Industry/Entity Type

Custom software development and Bitcoin

Contact Information for Business Card

Dale Parker, dale@vextorial.com, vextorial.com, (888) 555-VXTRL

Font styles to use
Other font styles liked:
• monospace

Requirements
Must have
• double-sided
Nice to have
• clean and simple
Should not have
• physical address

```html
<!DOCTYPE html>
<html lang="en">
<head>
<meta charset="utf-8">
<title>Vextorial — Business Card</title>
<link rel="stylesheet" href="https://fonts.googleapis.com/css2?family=Open+Sans:wght@400;800&family=Courier+Prime:wght@400;700&display=swap">
<style>
  :root {
    --backdrop: #4a4a49;
    --card-dark: #181818;
    --brand-orange: #f07c22;
    --brand-blue: #3d70b8;
    --paper-white: #ffffff;
    --font-text: "Open Sans", Arial, sans-serif;
    --font-mono: "Courier Prime", "Courier New", monospace;
  }
  * { box-sizing: border-box; margin: 0; padding: 0; }
  html, body {
    width: 1200px; height: 801px; overflow: hidden;
    background: var(--backdrop);
  }
  .canvas { position: relative; width: 1200px; height: 801px; }

  .card {
    position: absolute;
    width: 560px; height: 320px;
    overflow: hidden;
  }

  /* Front side */
  .card--front {
    left: 40px; top: 70px;
    background: var(--card-dark);
    border-right: 3px solid var(--brand-orange);
    border-bottom: 3px solid var(--brand-orange);
  }
  .front__mark {
    position: absolute; right: 96px; top: 22px;
    width: 104px; height: 104px;
    background: var(--brand-blue);
  }
  .front__brand {
    position: absolute; left: 40px; top: 66px;
  }
  .wordmark {
    font-family: var(--font-text);
    font-weight: 800;
    font-size: 44px;
    letter-spacing: 1px;
    line-height: 1;
    color: var(--brand-blue);
  }
  .tagline {
    font-family: var(--font-text);
    font-weight: 400;
    font-size: 16px;
    color: var(--brand-blue);
    margin-top: 4px;
    margin-left: 2px;
  }
  .person {
    position: absolute; left: 40px; right: 34px; top: 158px;
  }
  .person__headline {
    display: flex; align-items: center; gap: 10px;
  }
  .person__name {
    font-family: var(--font-mono);
    font-weight: 700;
    font-size: 22px;
    color: var(--brand-orange);
    white-space: nowrap;
  }
  .person__rule {
    flex: 1; height: 1.5px; background: var(--brand-orange);
  }
  .person__role {
    font-family: var(--font-mono);
    font-size: 14px;
    color: var(--paper-white);
    margin-top: 2px;
  }
  .contacts {
    position: absolute; left: 40px; top: 232px;
    list-style: none;
  }
  .contacts li {
    display: flex; align-items: center; gap: 8px;
    font-family: var(--font-mono);
    font-size: 13px;
    color: var(--paper-white);
    line-height: 20px;
  }
  .contacts svg { width: 12px; height: 12px; fill: var(--brand-orange); }
  .services {
    position: absolute; right: 34px; top: 208px;
    font-family: var(--font-mono);
    font-size: 12px;
    line-height: 17px;
    color: var(--paper-white);
    text-align: right;
    list-style: none;
  }
  .services__title {
    color: var(--brand-orange);
    font-weight: 700;
  }
  .front__tab {
    position: absolute; left: 0; bottom: 0;
    width: 22px; height: 28px;
    background: var(--brand-orange);
  }

  /* Back side */
  .card--back {
    left: 600px; top: 410px;
    background: var(--brand-orange);
    border-bottom: 3px solid var(--brand-blue);
    padding: 0 46px;
    display: flex; flex-direction: column;
    justify-content: center; align-items: flex-start;
  }
  .card--back .wordmark {
    color: var(--paper-white);
    font-size: 70px;
    letter-spacing: 2px;
  }
  .card--back .tagline {
    color: var(--paper-white);
    font-size: 27px;
    margin-top: 6px;
  }
</style>
</head>
<body>
<main class="canvas">

  <section class="card card--front" aria-label="Business card front">
    <div class="front__mark"></div>

    <div class="front__brand">
      <p class="wordmark">VEXTORIAL</p>
      <p class="tagline">developer of custom applications</p>
    </div>

    <div class="person">
      <div class="person__headline">
        <p class="person__name">Dale Parker</p>
        <span class="person__rule"></span>
      </div>
      <p class="person__role">Founding Partner</p>
    </div>

    <ul class="contacts">
      <li>
        <svg viewBox="0 0 24 24" aria-hidden="true"><path d="M6.6 10.8a15.1 15.1 0 0 0 6.6 6.6l2.2-2.2a1 1 0 0 1 1-.25 11.4 11.4 0 0 0 3.6.57 1 1 0 0 1 1 1V20a1 1 0 0 1-1 1A17 17 0 0 1 3 4a1 1 0 0 1 1-1h3.5a1 1 0 0 1 1 1c0 1.25.2 2.45.57 3.57a1 1 0 0 1-.25 1z"/></svg>
        (888) 555-VXTRL
      </li>
      <li>
        <svg viewBox="0 0 24 24" aria-hidden="true"><path d="M2 5h20v14H2z"/><path d="M2 5l10 8 10-8" fill="none" stroke="#181818" stroke-width="2"/></svg>
        dale@vextorial.com
      </li>
      <li>
        <svg viewBox="0 0 24 24" aria-hidden="true"><circle cx="12" cy="12" r="10"/></svg>
        www.vextorial.com
      </li>
    </ul>

    <ul class="services">
      <li class="services__title">Bitcoin services</li>
      <li>education &amp; secure custody</li>
      <li>payment integration</li>
    </ul>

    <div class="front__tab"></div>
  </section>

  <section class="card card--back" aria-label="Business card back">
    <p class="wordmark">VEXTORIAL</p>
    <p class="tagline">developer of custom applications</p>
  </section>

</main>
</body>
</html>
```